House-share and Room Rental Website (With Focus on the Bedroom Landing Page)

Looking for website design for our House-share (executive accommodation) and room rental business.

Our Lodgivo is: Lodgivo could also be written as LodGivo or lodgivo. Either is fine .. just looking for a nice clean catchy logo to go with the design.

EXAMPLES
These are examples of other websites in this field that are doing well. this is a kind of baseline.
https://nestpartners-example.com.au/
https://www.bunkora-example.com/
https://www.dwelzy-example.com/
https://www.habiquo-example.net/
https://www.cohabiscout-example.com.au/

Our business model is to rent rooms to people looking for high-quality accommodation. We fill the gap between those looking to rent rooms and those with rooms to rent. However, our model is slightly different from those already on the market as we looking to fill a massive gap in the market delivering upmarket rooms for rent.(Executive Accommodation) also in the back end will be coupled with a self management process in the back end.

We offer executive style accommodation that stands out above the rest. With special extras like fire safety.. and management processes that create happier homes. We are looking for a web design package that can help us grow and scale our business. We need a design that is captivating

Our MAIN focus is having a room landing page that stands out from the rest... The core of our business will rely on the promotion of the rooms in a share house... so the whole design relies on the BEDROOM landing page to drive results.

Target Market(s)

We have 2 markets we are aiming at ... the first market is people offering rooms to rent who want the highest rental return. The second market is people looking to rent safe, high-quality rooms, in houses that are well managed and looked after.

Industry/Entity Type

Share Economy

Logo Text

LodGivo

Number of Pages Required

5+ page

Font styles to use
Sans Serif

Colors
3276b5

Requirements
Must have
• A messaging system whereby we can create direct communication between those offering rooms and those looking for rooms.
• A call to action that says " Schedule an Inspection"
• Landing page for promoting rooms
• A home page for showing stock.
• Profile page for those selling rooms
• Profile page for those looking for rooms.
• A scheduling calendar for booking inspections
Nice to have
• Pages where new residents can lock in a room.. pay bond and rents.. and sign contracts
• Notifications
• SMS capabilities in the backend.
Should not have
• No script or handwriting fonts.

```html
<!DOCTYPE html>
<html lang="en">
<head>
<meta charset="utf-8">
<title>Lodgivo – Room Rental</title>
<link href="https://fonts.googleapis.com/css2?family=Roboto+Condensed:wght@400;700&family=Lato:wght@400;700&display=swap" rel="stylesheet">
<style>
:root{
  --blue:#2e6db4;
  --ink:#2b2b2b;
  --text:#555;
  --light:#f2f2f2;
  --footer:#1a1a1a;
  --white:#fff;
  --press:#2a2a2a;
}
*{box-sizing:border-box;margin:0;padding:0}
html,body{width:1200px;height:4455px;overflow:hidden}
body{font-family:"Lato",sans-serif;color:var(--text);background:var(--white);position:relative}
section,header,footer{position:absolute;left:0;width:1200px}
.h2{font-family:"Roboto Condensed",sans-serif;font-weight:700;font-size:50px;text-transform:uppercase;text-align:center;letter-spacing:.5px}
.h2.blue{color:var(--blue)}
.h2.white{color:var(--white)}
.btn-outline{display:inline-block;border:2px solid var(--blue);color:var(--blue);font-family:"Roboto Condensed",sans-serif;font-weight:700;font-size:15px;letter-spacing:.5px;text-transform:uppercase;text-align:center}
.btn-solid{display:inline-block;background:var(--blue);color:var(--white);font-family:"Roboto Condensed",sans-serif;font-weight:700;font-size:17px;text-transform:uppercase;text-align:center}
.photo{display:block}
.dots{position:absolute;left:0;width:1200px;display:flex;justify-content:center;gap:8px}
.dots span{width:30px;height:5px;background:var(--white)}
.dots span.on{background:var(--blue)}

/* header */
.site-header{top:0;height:118px;display:flex;align-items:center;justify-content:space-between;padding:0 75px}
.logo{font-family:"Roboto Condensed",sans-serif;font-weight:700;font-size:36px;color:var(--ink);letter-spacing:.5px}
.nav{display:flex;gap:44px;font-family:"Roboto Condensed",sans-serif;font-weight:700;font-size:13px;text-transform:uppercase;color:var(--ink)}
.nav .active{color:var(--blue)}

/* hero */
.hero{top:118px;height:542px;background:linear-gradient(100deg,#6b6e70 0%,#8d8c88 35%,#5f6a62 60%,#8a8f88 80%,#bdbfb8 100%)}
.hero .shade{position:absolute;inset:0;background:rgba(0,0,0,.28)}
.hero-content{position:absolute;top:172px;left:0;width:1200px;text-align:center;color:var(--white)}
.hero-title{font-family:"Roboto Condensed",sans-serif;font-weight:700;font-size:72px;line-height:1}
.hero-sub{font-family:"Lato",sans-serif;font-weight:700;font-size:24px;margin-top:22px}
.hero .btn-solid{margin-top:28px;width:268px;height:52px;line-height:52px}
.arrow{position:absolute;top:250px}

/* welcome */
.welcome{top:660px;height:413px;text-align:center}
.welcome .h2{margin-top:64px}
.welcome p{width:1040px;margin:22px auto 0;font-size:16px;line-height:26px}
.welcome .btn-outline{margin-top:40px;width:178px;height:48px;line-height:44px}

/* rooms */
.rooms{top:1073px;height:712px;background:linear-gradient(180deg,#2a2a2a,#3a3a3a 50%,#242424)}
.rooms .h2{position:absolute;top:52px;width:1200px}
.card-row{position:absolute;top:149px;left:75px;display:flex;gap:30px}
.room-card{width:330px;height:416px;background:var(--white);text-align:center}
.room-card .photo{width:330px;height:205px}
.room-card h3{font-family:"Roboto Condensed",sans-serif;font-weight:700;font-size:24px;color:var(--blue);text-transform:uppercase;margin-top:22px}
.room-card p{width:290px;margin:10px auto 0;font-size:14px;line-height:21px}
.room-card .btn-outline{margin-top:22px;width:140px;height:36px;line-height:32px;font-size:14px}
.rooms .dots{top:634px}

/* why us */
.why{top:1785px;height:465px}
.why-text{position:absolute;left:75px;top:90px;width:520px}
.why-text .h2{text-align:left}
.why-text p{margin-top:26px;font-size:16px;line-height:25px}
.why-text .btn-outline{margin-top:36px;width:178px;height:48px;line-height:44px}
.why .photo{position:absolute;left:615px;top:75px;width:510px;height:310px}

/* testimonials */
.testimonials{top:2250px;height:715px;background:linear-gradient(180deg,#242424,#333 50%,#1f1f1f)}
.testimonials .h2{position:absolute;top:52px;width:1200px}
.t-grid{position:absolute;top:148px;left:75px;display:grid;grid-template-columns:525px 525px;column-gap:25px;row-gap:22px}
.t-card{height:208px;display:flex;background:var(--white)}
.t-card .photo{width:245px;height:208px;flex:none}
.t-copy{padding:22px 20px 0 24px;font-size:14px;line-height:22px;flex:1}
.t-name{margin-top:12px;font-family:"Roboto Condensed",sans-serif;font-weight:700;font-size:14px;color:var(--blue);text-transform:uppercase}
.testimonials .dots{top:642px}

/* press */
.press{top:2965px;height:325px;text-align:center}
.press .h2{margin-top:52px;font-size:34px}
.press-row{display:flex;justify-content:center;align-items:center;gap:56px;margin-top:32px}
.press-row + .press-row{margin-top:34px}
.press-name{font-family:"Roboto Condensed",sans-serif;font-weight:700;font-size:26px;color:var(--press)}

/* blog */
.blog{top:3290px;height:585px;background:var(--light)}
.blog .h2{position:absolute;top:60px;width:1200px}
.blog-row{position:absolute;top:147px;left:75px;display:flex;gap:30px}
.post{width:330px;text-align:center}
.post .photo{width:330px;height:203px}
.post h3{font-family:"Roboto Condensed",sans-serif;font-weight:700;font-size:24px;color:var(--blue);text-transform:uppercase;margin-top:26px}
.post p{margin-top:10px;font-size:15px;line-height:23px;color:#444}
.more{display:inline-block;margin-top:18px;font-family:"Roboto Condensed",sans-serif;font-weight:700;font-size:14px;color:var(--blue);text-transform:uppercase}

/* newsletter */
.newsletter{top:3875px;height:305px;text-align:center}
.newsletter .h2{margin-top:48px;font-size:34px}
.newsletter p{margin-top:10px;font-size:15px;color:#444}
.email{margin:22px auto 0;width:690px;height:48px;border:1px solid #ccc;text-align:left;padding:0 16px;line-height:46px;font-size:13px;color:#888}
.newsletter .btn-solid{margin-top:22px;width:170px;height:44px;line-height:44px;font-size:15px}

/* footer */
.site-footer{top:4180px;height:275px;background:var(--footer);color:#aaa}
.f-logo{position:absolute;left:75px;top:105px;font-family:"Roboto Condensed",sans-serif;font-weight:700;font-size:36px;color:#555}
.f-legal{position:absolute;left:75px;top:152px;font-size:12px;line-height:17px;color:#777}
.f-col{position:absolute;top:48px;font-size:13px;line-height:23px}
.f-col h4{font-family:"Roboto Condensed",sans-serif;font-weight:700;font-size:19px;color:var(--white);text-transform:uppercase;margin-bottom:6px}
.f-col ul{list-style:none}
.f-contact li{display:flex;gap:18px;align-items:flex-start;margin-bottom:6px;line-height:17px}
.social{display:flex;gap:16px;margin-top:10px}
.social span{width:18px;height:18px;background:var(--white)}
</style>
</head>
<body>

<header class="site-header">
  <div class="logo">LODGIVO</div>
  <nav class="nav">
    <span class="active">Home</span><span>About Us</span><span>Rental Rooms</span><span>Testimonials</span><span>Blog</span><span>Contact Us</span>
  </nav>
</header>

<section class="hero">
  <div role="img" aria-label="Modern bedroom with a low wooden bed and large windows onto a garden" style="position:absolute;inset:0"></div>
  <div class="shade"></div>
  <svg class="arrow" style="left:58px" width="26" height="42" viewBox="0 0 26 42"><path d="M22 3 L5 21 L22 39" fill="none" stroke="#fff" stroke-width="4"/></svg>
  <svg class="arrow" style="right:58px" width="26" height="42" viewBox="0 0 26 42"><path d="M4 3 L21 21 L4 39" fill="none" stroke="#fff" stroke-width="4"/></svg>
  <div class="hero-content">
    <div class="hero-title">HOUSE-SHARE</div>
    <div class="hero-sub">Aliquam augue nisl, tempus a vestibulum ultricies interdum id ex.</div>
    <span class="btn-solid">Schedule an Inspection</span>
  </div>
</section>

<section class="welcome">
  <h2 class="h2 blue">Welcome to Our Website</h2>
  <p>Lorem ipsum dolor sit amet, consectetur adipiscing elit. Aenean interdum, justo eget ullamcorper feugiat, magna sapien auctor magna, eget iaculis dui arcu congue risus. Maecenas tempus mattis sagittis. Integer lobortis ex nunc, ut luctus mauris congue a. Quisque tincidunt orci vitae sapien varius, nec imperdiet erat tincidunt. Suspendisse ultricies, mauris et viverra sagittis, arcu odio luctus massa, ac sagittis velit nibh et justo.</p>
  <span class="btn-outline">Read More</span>
</section>

<section class="rooms">
  <h2 class="h2 white">Room Rental</h2>
  <div class="card-row">
    <article class="room-card">
      <div class="photo" role="img" aria-label="Bedroom with a grey platform bed" style="background:linear-gradient(160deg,#8d8f90,#c9c6c0 60%,#6d5a4c)"></div>
      <h3>Fusce Aliquet</h3>
      <p>Vestibulum ante ipsum primis in faucibus orci luctus et ultrices iaculis posuere augue lacinia luctus..</p>
      <span class="btn-outline">More Info ➜</span>
    </article>
    <article class="room-card">
      <div class="photo" role="img" aria-label="Bright bedroom with white bedding and framed pictures" style="background:linear-gradient(160deg,#6a5c50,#d8d4cc 55%,#8f8679)"></div>
      <h3>Fusce Aliquet</h3>
      <p>Vestibulum ante ipsum primis in faucibus orci luctus et ultrices iaculis posuere augue lacinia luctus..</p>
      <span class="btn-outline">More Info ➜</span>
    </article>
    <article class="room-card">
      <div class="photo" role="img" aria-label="Classic bedroom with cream bed and chandelier" style="background:linear-gradient(160deg,#5a4a3e,#c8b9a4 55%,#e4dccf)"></div>
      <h3>Fusce Aliquet</h3>
      <p>Vestibulum ante ipsum primis in faucibus orci luctus et ultrices iaculis posuere augue lacinia luctus..</p>
      <span class="btn-outline">More Info ➜</span>
    </article>
  </div>
  <div class="dots"><span class="on"></span><span></span><span></span><span></span></div>
</section>

<section class="why">
  <div class="why-text">
    <h2 class="h2 blue">Why Us</h2>
    <p>Aliquam molestie, mi et imperdiet euismod, dui purus auctor tellus, et interdum lacus lectus et ante. Sed accumsan sollicitudin sapien, sit amet adipiscing turpis gravida ac. In congue, neque ac lobortis volutpat, libero mauris varius mi..</p>
    <span class="btn-outline">Read More</span>
  </div>
  <div class="photo" role="img" aria-label="Hands on a laptop showing a house listing" style="background:linear-gradient(135deg,#e9e6e0,#c9c2b6 45%,#8a7d6a 75%,#f2f0ec)"></div>
</section>

<section class="testimonials">
  <h2 class="h2 white">Testimonials</h2>
  <div class="t-grid">
    <div class="t-card">
      <div class="t-copy">" Vestibulum ante ipsum primis in faucibus orci luctus et ultrices iaculis scelerisque rhoncus sapien ac ultrices. Nullam tempor sed risus sed laoreet."<div class="t-name">- Name Heading</div></div>
      <div class="photo" role="img" aria-label="Portrait of a smiling customer" style="background:linear-gradient(180deg,#ececec,#d9c3b0 60%,#f4f4f4)"></div>
    </div>
    <div class="t-card">
      <div class="photo" role="img" aria-label="Portrait of a customer in a suit" style="background:linear-gradient(180deg,#dcdcdc,#c9ad98 50%,#2c3340)"></div>
      <div class="t-copy">" Vestibulum ante ipsum primis in faucibus orci luctus et ultrices iaculis scelerisque rhoncus sapien ac ultrices. Nullam tempor sed risus sed laoreet."<div class="t-name">- Name Heading</div></div>
    </div>
    <div class="t-card">
      <div class="t-copy">" Vestibulum ante ipsum primis in faucibus orci luctus et ultrices iaculis scelerisque rhoncus sapien ac ultrices. Nullam tempor sed risus sed laoreet."<div class="t-name">- Name Heading</div></div>
      <div class="photo" role="img" aria-label="Portrait of a smiling customer" style="background:linear-gradient(180deg,#f0f0f0,#5a4436 40%,#d7b8a0 70%,#2a2a2a)"></div>
    </div>
    <div class="t-card">
      <div class="photo" role="img" aria-label="Portrait of a smiling customer" style="background:linear-gradient(180deg,#eaeaea,#6a5240 35%,#d4b39a 65%,#e5e5e5)"></div>
      <div class="t-copy">" Vestibulum ante ipsum primis in faucibus orci luctus et ultrices iaculis scelerisque rhoncus sapien ac ultrices. Nullam tempor sed risus sed laoreet."<div class="t-name">- Name Heading</div></div>
    </div>
  </div>
  <div class="dots"><span class="on"></span><span></span><span></span><span></span></div>
</section>

<section class="press">
  <h2 class="h2 blue">As Seen On</h2>
  <div class="press-row">
    <span class="press-name">Northleaf Press Group</span>
    <span class="press-name">The Harbor Ledger</span>
    <span class="press-name">Quickline Weekly</span>
  </div>
  <div class="press-row">
    <span class="press-name">The Market Street Gazette</span>
    <span class="press-name">Newscove</span>
    <span class="press-name">The Evening Hound</span>
  </div>
</section>

<section class="blog">
  <h2 class="h2 blue">Blog</h2>
  <div class="blog-row">
    <article class="post">
      <div class="photo" role="img" aria-label="Bedroom with a low wooden bed and grey wall" style="background:linear-gradient(160deg,#9a9590,#c9c2b7 55%,#6c5742)"></div>
      <h3>Lorem Ipsum Dolor Sit Amet</h3>
      <p>Vestibulum ante ipsum primis in faucibus orci luctus et ultrices iaculis nibh eget turpis vehicula tempus ac sed..</p>
      <span class="more">More Info ➜</span>
    </article>
    <article class="post">
      <div class="photo" role="img" aria-label="Bedroom with green bedding and tall windows" style="background:linear-gradient(160deg,#4a3a2a,#8c8a5a 50%,#c7c0a8)"></div>
      <h3>Lorem Ipsum Dolor Sit Amet</h3>
      <p>Vestibulum ante ipsum primis in faucibus orci luctus et ultrices iaculis nibh eget turpis vehicula tempus ac sed..</p>
      <span class="more">More Info ➜</span>
    </article>
    <article class="post">
      <div class="photo" role="img" aria-label="Bedroom with dark feature wall and white bed" style="background:linear-gradient(160deg,#3d2e28,#7a5d52 45%,#e6e1dc)"></div>
      <h3>Lorem Ipsum Dolor Sit Amet</h3>
      <p>Vestibulum ante ipsum primis in faucibus orci luctus et ultrices iaculis nibh eget turpis vehicula tempus ac sed..</p>
      <span class="more">More Info ➜</span>
    </article>
  </div>
</section>

<section class="newsletter">
  <h2 class="h2 blue">Newsletter Sign Up</h2>
  <p>Vestibulum ante ipsum primis in faucibus orci luctus et ultrices iaculis nibh eget turpis vehicula tempus ac sed..</p>
  <div class="email">Email Address Address</div>
  <span class="btn-solid">Subscribe Now</span>
</section>

<footer class="site-footer">
  <div class="f-logo">LODGIVO</div>
  <div class="f-legal">Copyright © 2019, Lodgivo<br>All Right Reserved</div>
  <div class="f-col" style="left:365px">
    <h4>Site Map</h4>
    <ul><li>Home</li><li>About Us</li><li>Rental Rooms</li><li>Testimonials</li><li>Blog</li><li>Contact Us</li></ul>
  </div>
  <div class="f-col" style="left:612px">
    <h4>Site Map</h4>
    <ul class="f-contact">
      <li><svg width="12" height="16" viewBox="0 0 12 16"><path d="M6 0a6 6 0 0 0-6 6c0 4.5 6 10 6 10s6-5.5 6-10a6 6 0 0 0-6-6zm0 8.5A2.5 2.5 0 1 1 6 3.5a2.5 2.5 0 0 1 0 5z" fill="#ccc"/></svg><span>14 Elmview Lane, Brookfield Avenue<br>Riverton City</span></li>
      <li><svg width="14" height="14" viewBox="0 0 14 14"><path d="M3 0l2.5 3.5-1.5 2a8 8 0 0 0 4.5 4.5l2-1.5L14 11l-2 3C5.5 14 0 8.5 0 2z" fill="#ccc"/></svg><span>1-800-555-0142</span></li>
      <li><svg width="14" height="11" viewBox="0 0 14 11"><rect width="14" height="11" fill="#ccc"/><path d="M0 0l7 6 7-6" fill="none" stroke="#1a1a1a" stroke-width="1.5"/></svg><span>hello@lodgivo-example.com</span></li>
    </ul>
  </div>
  <div class="f-col" style="left:930px">
    <h4>Follow Us</h4>
    <div class="social" aria-label="Social links"><span></span><span></span><span></span><span></span><span></span></div>
  </div>
</footer>

</body>
</html>
```